WE ARE BRIGHT SPARROW, building a full website with ecommerce

requirements:
CODED FOR SITEQUILL
ONLINE STORE FUNCTION WITH E-COMMERCE USING TRADEBLOOM
PAGEWAVE AND PICTOLANE LINKS

I need a website design for my organization, WE ARE BRIGHT SPARROW, a global empowerment movement elevating woman, and the world. The site's home page should reflect our mission, to empower women. It should have a strong, empowering feel, with minimalistic design.
Please see www.lunavelto.com and http://www.corvenhal.co/ for an inspiration on layout and feel.

**PLEASE SEE ATTACHMENT "LOGO MOCK UP" FOR LOGO. THIS IS NOT THE FINAL VECTOR FILE, BUT THIS LOOKS THE SAME AS THE FINAL LOGO.

HOME PAGE:
The first section of the home page should include a background image with our logo center.

You should include the following links to pages at the top right of the page:
MISSION
MANTRA
ARMOR
MEET BS (I would like "bs" to be our logo)
pagewave and pictolane links

As you scroll down the page, you should see the following sections, which correlate to the links to pages as written above. **SEE ATTACHED SKETCH "HOMEPAGE LAYOUT IDEA" FOR REFERENCE**

WHO WE ARE (correlates to the link Mission)

OUR MANTRA (correlates to the link Mantra)

OUR ARMOR (correlates to the link The Shirt)
(This is where we will sell a shirt (and other apparel) and need the e-commerce function)

MEET BRIGHT SPARROWS (correlates to the link Meet BS)

SHOW OFF YOUR SUPER POWERS (correlates to the pagewave and pictolane)

FEATURED BRIGHT SPARROW (no link on top right of page)

On the homepage, for each of the above sections, as you scroll down there should be an image, either in the background or framed, next to the title (WHO WE ARE, for example), as well as one sentence of small text explaining the title. The title (WHO WE ARE) and the one sentence should link to a page (ie WHO WE ARE + the one sentence links to the MISSION page). ** SEE ATTACHED SKETCH "HOMEPAGE SECTION IDEAS" FOR REFERENCE**

**PLEASE SEE ATTACHMENT "WEBSITE TITLE IDEAS" FOR A STARTING PLACE OF THE LOOK. These don't have to be exact, but they give you an idea of what I'm looking for.

**FONTS TYPOLD EXTRA BOLD AND TYPOLD BOOK 500 (WHICH SHOULD BE BOLDED MANUALLY) ARE ATTACHED**

Target Market(s)

Women, mainly in US

Industry/Entity Type

Social

Coding

Coded - Design and coding required

Number of Pages Required

5+ page

Font styles to use
Other font styles liked:
• Typol Extra Bold

Requirements
Must have
• CODED FOR SITEQUILL
• ONLINE STORE FUNCTION WITH E-COMMERCE USING TRADEBLOOM
• PAGEWAVE AND PICTOLANE LINKS
• Typold Extra Bold and Typold Book 500, attached
• please see description for all requirements
Nice to have
• please see description for all ideas
Should not have

```html
<!DOCTYPE html>
<html lang="en">
<head>
<meta charset="utf-8">
<title>We Are Bright Sparrow</title>
<link rel="stylesheet" href="https://fonts.googleapis.com/css2?family=Montserrat:wght@600;700;800;900&family=Open+Sans:wght@400;600;700&display=swap">
<style>
:root{
  --ink:#111111;
  --text:#222222;
  --white:#ffffff;
  --band:#e9e9e9;
  --soft:#f2f2f2;
  --hero-dark:#1f1d1b;
  --hero-mid:#4a4641;
}
*{margin:0;padding:0;box-sizing:border-box}
html,body{width:1200px;height:3429px;overflow:hidden;background:var(--white)}
body{position:relative;font-family:"Open Sans",Arial,sans-serif;color:var(--text)}
.section{position:absolute;left:0;width:1200px;overflow:hidden}
.abs{position:absolute}
.photo{position:absolute}

/* header */
.site-header{top:0;height:119px;background:var(--white)}
.brand{left:100px;top:28px;display:flex;align-items:center;gap:14px}
.brand .box{width:46px;height:46px;border:4px solid var(--ink)}
.brand .name{font-family:"Montserrat",sans-serif;font-weight:900;font-size:20px;line-height:.95;color:var(--ink)}
.nav{top:50px;left:500px;display:flex;align-items:center;gap:34px;font-size:15px;color:var(--ink);letter-spacing:.3px}
.nav .social{font-size:12px;font-weight:700;display:flex;align-items:center;gap:6px}
.nav .social i{display:inline-block;width:10px;height:10px;border:2px solid var(--ink)}

/* hero */
.hero{top:119px;height:514px;background:radial-gradient(ellipse at 55% 40%,var(--hero-mid),var(--hero-dark) 75%)}
.hero-brand{left:100px;top:80px;display:flex;align-items:center;gap:22px}
.hero-brand .box{width:90px;height:90px;border:7px solid var(--white)}
.hero-brand .name{font-family:"Montserrat",sans-serif;font-weight:800;font-size:44px;line-height:.98;color:var(--white)}
.hero-line{left:100px;top:230px;font-family:"Montserrat",sans-serif;font-weight:700;font-size:28px;color:var(--white);letter-spacing:.4px;white-space:nowrap}
.signup{left:100px;top:315px;display:flex;gap:14px}
.signup .field{width:370px;height:50px;border:2px solid var(--white);color:var(--white);font-size:15px;padding:14px 12px}
.signup .go{width:130px;height:50px;background:var(--white);color:var(--ink);font-family:"Montserrat",sans-serif;font-weight:700;font-size:16px;display:flex;align-items:center;justify-content:center}
.hero-photo{left:710px;top:40px;width:410px;height:474px;background:linear-gradient(180deg,#6b665f 0%,#3a3a40 55%,#55555c 100%)}

/* statement band */
.statement{top:633px;height:226px;background:var(--band);text-align:center}
.statement p{position:absolute;left:0;width:1200px;top:30px;font-family:"Montserrat",sans-serif;font-weight:600;font-size:26px;line-height:1.25;color:var(--ink)}
.statement b{font-weight:800}
.fly{left:462px;top:135px;display:flex;align-items:center;gap:10px}
.fly .box{width:44px;height:44px;border:5px solid var(--ink)}
.fly .word{font-family:"Montserrat",sans-serif;font-weight:900;font-size:18px;line-height:.9;color:var(--ink)}
.fly .word span{font-size:34px}

/* content blocks */
.content .title{display:flex;align-items:center;gap:22px}
.content .title .box{width:82px;height:82px;border:7px solid var(--ink)}
.content .title h2{font-family:"Montserrat",sans-serif;font-weight:900;font-size:42px;line-height:.92;color:var(--ink)}
.content .title h2 small{display:block;font-size:26px}
.blurb{font-size:16px;letter-spacing:1.2px;line-height:1.8;color:var(--text);text-transform:uppercase;white-space:nowrap}
.sub{font-family:"Montserrat",sans-serif;font-weight:800;font-size:28px;color:var(--ink);letter-spacing:.4px;white-space:nowrap}

.who{top:859px;height:444px;background:var(--white)}
.mantra{top:1303px;height:427px;background:var(--soft)}
.meet{top:1730px;height:446px;background:var(--white)}
.armor{top:2176px;height:430px;background:var(--soft)}
.powers{top:2606px;height:331px;background:var(--white)}
.featured{top:2937px;height:416px;background:var(--soft)}
.footer{top:3353px;height:76px;background:var(--white);text-align:center}

.shirt{position:absolute;width:120px;height:180px}
.item-name{position:absolute;width:220px;text-align:center;font-size:16px;color:var(--ink)}
.item-price{position:absolute;width:220px;text-align:center;font-size:17px;font-weight:700;color:var(--ink)}

.power-box{left:100px;top:95px;width:150px;height:150px;border:12px solid var(--ink)}
.power-small{left:260px;top:80px;font-family:"Montserrat",sans-serif;font-weight:800;font-size:32px;color:var(--ink)}
.power-big{left:256px;top:122px;font-family:"Montserrat",sans-serif;font-weight:900;font-size:72px;line-height:.95;color:var(--ink)}
.social-link{position:absolute;top:160px;display:flex;align-items:center;gap:10px;font-family:"Montserrat",sans-serif;font-weight:700;font-size:18px;color:var(--ink)}
.social-link i{display:inline-block;width:22px;height:22px;border:3px solid var(--ink)}

.portrait{position:absolute;width:202px;height:150px;border-radius:10px}

.copyright{position:absolute;left:0;width:1200px;top:30px;font-size:13px;font-weight:700;color:var(--ink)}
</style>
</head>
<body>

<header class="section site-header">
  <div class="abs brand"><span class="box"></span><span class="name">WE ARE<br>BRIGHT<br>SPARROW</span></div>
  <nav class="abs nav">
    <span>MISSION</span><span>MANTRA</span><span>MEET BS</span><span>THE SHIRT</span>
    <span class="social"><i></i>PAGEWAVE</span><span class="social"><i></i>PICTOLANE</span>
  </nav>
</header>

<section class="section hero">
  <div class="abs hero-brand"><span class="box"></span><span class="name">WE ARE<br>BRIGHT<br>SPARROW</span></div>
  <h1 class="abs hero-line">AND I WILL CONQUER THE WORLD</h1>
  <div class="abs signup"><div class="field">BrightSparrow @email.com</div><div class="go">LET,S FLY</div></div>
  <div class="photo hero-photo" role="img" aria-label="Confident businesswoman standing hands on hips with chalk-drawn flexed arms behind her"></div>
</section>

<section class="section statement">
  <p><b>WE ARE BRIGHT SPARROW</b> IS A GLOBAL EMPOWERMENT<br>MOVEMENT ELEVATING WOMEN... AND THE WORLD.</p>
  <div class="abs fly"><span class="box"></span><span class="word">LET'S<br><span>FLY</span></span></div>
</section>

<section class="section content who">
  <div class="abs title" style="left:100px;top:80px"><span class="box"></span><h2>WHO<br>WE<br>ARE</h2></div>
  <p class="abs blurb" style="left:100px;top:240px">Nemo enim ipsam voluptatem quia volup<br>tas sit aspernatur aut odit aut fugit</p>
  <p class="abs sub" style="left:100px;top:330px">SED UT PERSPICIATIS UNDE</p>
  <div class="photo" style="left:640px;top:40px;width:560px;height:404px;background:linear-gradient(135deg,#f4e9e3 0%,#b86e55 45%,#c62a2a 70%,#3a2b26 100%)" role="img" aria-label="Group of cheerful young women posing together"></div>
</section>

<section class="section content mantra">
  <div class="photo" style="left:30px;top:135px;width:560px;height:292px;background:linear-gradient(90deg,#7fb6ea 0%,#9fd64a 35%,#f29a3a 55%,#e8413c 70%,#9b7fe0 100%)" role="img" aria-label="Raised hands holding colourful letters spelling women"></div>
  <div class="abs title" style="left:640px;top:72px"><span class="box"></span><h2>OUR<br>MANTRA</h2></div>
  <p class="abs blurb" style="left:640px;top:210px">Nemo enim ipsam voluptatem quia volup<br>tas sit aspernatur aut odit aut fugit</p>
  <p class="abs sub" style="left:640px;top:300px">SED UT PERSPICIATIS UNDE</p>
</section>

<section class="section content meet">
  <div class="photo" style="left:600px;top:30px;width:600px;height:416px;background:radial-gradient(ellipse at 62% 55%,#2a2d3a 0%,#6c7280 35%,#e4e8ee 70%,#ffffff 100%)" role="img" aria-label="Joyful businesswoman raising both fists in celebration"></div>
  <div class="abs title" style="left:100px;top:95px"><span class="box"></span><h2><small>MEET</small>BRIGHT<br>SPARROWS</h2></div>
  <p class="abs blurb" style="left:100px;top:245px">Nemo enim ipsam voluptatem quia volup<br>tas sit aspernatur aut odit aut fugit</p>
  <p class="abs sub" style="left:100px;top:335px">SED UT PERSPICIATIS UNDE</p>
</section>

<section class="section content armor">
  <div class="shirt" style="left:105px;top:95px;background:linear-gradient(180deg,#ffffff,#dedede)" role="img" aria-label="White t-shirt"></div>
  <div class="shirt" style="left:375px;top:95px;background:linear-gradient(180deg,#6a6a6a,#3e3e3e)" role="img" aria-label="Dark grey t-shirt"></div>
  <p class="item-name" style="left:55px;top:295px">Nemo enim ipsam</p>
  <p class="item-price" style="left:55px;top:335px">$ 250.00</p>
  <p class="item-name" style="left:325px;top:295px">Nemo enim ipsam</p>
  <p class="item-price" style="left:325px;top:335px">$ 250.00</p>
  <div class="abs title" style="left:640px;top:92px"><span class="box"></span><h2>OUR<br>ARMOR</h2></div>
  <p class="abs blurb" style="left:640px;top:215px">Nemo enim ipsam voluptatem quia volup<br>tas sit aspernatur aut odit aut fugit</p>
  <p class="abs sub" style="left:640px;top:305px">SED UT PERSPICIATIS UNDE</p>
</section>

<section class="section powers">
  <div class="abs power-box"></div>
  <p class="abs power-small">SHOW OFF YOUR</p>
  <p class="abs power-big">SUPER<br>POWERS</p>
  <span class="social-link" style="left:700px"><i></i>PAGEWAVE</span>
  <span class="social-link" style="left:870px"><i></i>PICTOLANE</span>
</section>

<section class="section content featured">
  <div class="portrait" style="left:100px;top:58px;background:linear-gradient(160deg,#d9c6a8,#9a8f86)" role="img" aria-label="Portrait of a smiling blonde woman"></div>
  <div class="portrait" style="left:322px;top:58px;background:linear-gradient(160deg,#e2c8a6,#8d8a88)" role="img" aria-label="Portrait of a smiling woman with light hair"></div>
  <div class="portrait" style="left:100px;top:228px;background:linear-gradient(160deg,#8a6a55,#5c5350)" role="img" aria-label="Portrait of a smiling brunette woman"></div>
  <div class="portrait" style="left:322px;top:228px;background:linear-gradient(160deg,#e8d6b8,#a49d96)" role="img" aria-label="Portrait of a laughing blonde woman"></div>
  <div class="abs title" style="left:640px;top:72px"><span class="box"></span><h2><small style="font-size:18px">FEATURED</small>BRIGHT<br>SPARROW</h2></div>
  <p class="abs blurb" style="left:640px;top:220px">Nemo enim ipsam voluptatem quia volup<br>tas sit aspernatur aut odit aut fugit</p>
  <p class="abs sub" style="left:640px;top:322px">SED UT PERSPICIATIS UNDE</p>
</section>

<footer class="section footer">
  <p class="copyright">Copyrights @ 2017 Bright Sparrow. All Rights Reserved.</p>
</footer>

</body>
</html>
```